Lantern Petals Website v.1 - attract floral shop franchisees

I need a simple information website for my new business. We are a franchisor of flower shops. The overall purpose of the website is to promote the company and the service, especially to potential franchisees and retailers. Only about 4 pages are required including homepage, About, For Supermarkets, For Franchisees, and Contact. No special functions are required except the site will have two separate inquiry forms that must be filled out online and submitted via automated email. Similarly, an email form should be linked from the Contact page. I have a logo and business cards designed by ArtMingle, and I would like the site to have a consistent color scheme and style. The key to design will be to express the joy and love associated with flowers and floral bouquets.
IMPORTANT - I will be exporting the website design to Wordpress CMS in a site hosted by HostNimbus. For smooth integration into WordPress hosted by HostNimbus, the designer should build the site using a WordPress-friendly format. Ideally, they should use HTML, CSS, and PHP. Creating a custom theme or using a page builder that exports to WordPress-compatible files is best. This ensures the site can be easily imported and managed within WordPress.

Target Market(s)

Potential franchisees (existing florists or creative types who might like to own a floral business) and supermarkets who might want us to run their floral department

Industry/Entity Type

Floral retailing

Requirements
Must have
• A brand theme that is beautiful, consistent throughout and builds on the logo design
Nice to have
• Show gender and ethnic diversity in customers and florists. Pictures of happy florists (for franchisees) and pictures of amazing floral department displays (for supermarkets)

```html
<!DOCTYPE html>
<html lang="en">
<head>
<meta charset="utf-8">
<title>Lantern Petals – Floral Franchising</title>
<link href="https://fonts.googleapis.com/css2?family=Lato:wght@400;700&family=Great+Vibes&display=swap" rel="stylesheet">
<style>
:root{
  --orange:#ef9d22;
  --green:#128a3c;
  --ink:#222;
  --hero-bg:#e3e6eb;
  --footer-bg:#e6e7eb;
  --white:#fff;
}
*{box-sizing:border-box;margin:0;padding:0}
html,body{width:1200px;height:2995px;overflow:hidden}
body{position:relative;font-family:'Lato',sans-serif;color:var(--ink);background:var(--white)}
.abs{position:absolute}
.btn{position:absolute;display:flex;align-items:center;justify-content:center;color:var(--white);font-weight:700;font-size:16px;background:var(--orange);text-decoration:none}
.btn--green{background:var(--green)}
.script{font-family:'Great Vibes',cursive;font-weight:400;line-height:1}
.orange{color:var(--orange)}
.green{color:var(--green)}
.body-text{font-size:14px;line-height:26.5px;color:#222}
.body-text p+p{margin-top:8px}

/* hero */
.hero{position:absolute;left:0;top:0;width:1200px;height:633px;background:var(--hero-bg);overflow:hidden}
.hero__blob{position:absolute;left:-60px;top:-120px;width:480px;height:260px;background:var(--white);border-radius:0 0 260px 200px / 0 0 200px 140px;transform:rotate(-8deg)}
.logo{position:absolute;display:flex;align-items:center;gap:10px;font-family:'Lato',sans-serif;font-weight:700;color:var(--orange)}
.logo__dot{width:34px;height:34px;border-radius:50%;background:var(--orange)}
.nav{position:absolute;top:28px;left:515px;display:flex;gap:40px;font-weight:700;font-size:16px;color:var(--green)}
.hero__photo{position:absolute;left:620px;top:100px;width:580px;height:533px;background:radial-gradient(circle at 45% 50%,#f3b3c3 0%,#e98aa4 35%,#9aa85a 70%,#d9dde3 100%)}
.hero__welcome{left:112px;top:186px;font-size:27px}
.hero__script{left:92px;top:218px;font-size:140px;color:var(--orange)}
.hero__caps{left:102px;top:362px;font-size:80px;color:var(--green);letter-spacing:1px}

/* about */
.about__photo{position:absolute;left:117px;top:736px;width:414px;height:414px;border-radius:50%;background:radial-gradient(circle at 50% 35%,#f4c3d0 0%,#d8a0b0 25%,#c9ccd4 55%,#bfc3cb 100%)}
.section-title{position:absolute;font-size:84px}

/* supermarkets */
.market{position:absolute;left:0;top:1249px;width:1200px;height:577px;background:linear-gradient(120deg,#efe9ef,#e6dde8 50%,#efeaf0)}
.checklist{position:absolute;left:110px;top:1590px;list-style:none;font-size:14px}
.checklist li{display:flex;align-items:center;gap:12px;height:34.3px}
.link-heading{position:absolute;left:112px;top:1543px;font-size:23px;color:var(--green);text-decoration:underline;text-underline-offset:4px}

/* franchisees */
.franch__photo{position:absolute;left:72px;top:1940px;width:414px;height:404px;background:radial-gradient(circle at 35% 20%,#f7a52a 0%,#e84a3a 25%,#f2f2f2 55%,#ffffff 100%)}

/* inquiry */
.inquiry-band{position:absolute;left:0;top:2509px;width:1200px;height:155px;background:#dfe1e6}
.inquiry{position:absolute;left:112px;top:2383px;width:977px;height:281px;background:linear-gradient(90deg,#f0f0f2,#e8e8ec)}
.inquiry__photo{position:absolute;left:638px;top:19px;width:302px;height:262px;background:radial-gradient(circle at 50% 35%,#f3a6a6 0%,#e99a94 35%,#c9a57c 65%,#ebebee 100%)}
.inquiry__title{position:absolute;left:33px;top:32px;font-size:64px;line-height:78px;color:#1b1b1b}

/* footer */
.footer{position:absolute;left:0;top:2664px;width:1200px;height:331px;background:var(--footer-bg)}
.footer h4{position:absolute;font-size:16px;font-weight:700;color:#1b1b1b}
.footer ul{position:absolute;list-style:none;font-size:13px}
.quick li{height:30.3px}
.contact li,.social li{display:flex;align-items:center;gap:14px}
.contact li{height:42.5px}
.social li{height:39.5px}
.icon{width:20px;height:20px;border-radius:50%;background:var(--green);display:flex;align-items:center;justify-content:center;flex:none}
.email-field{position:absolute;left:112px;top:2847px;width:268px;height:41px;background:var(--white);font-size:12px;display:flex;align-items:center;padding-left:18px}
.rule{position:absolute;left:110px;top:2955px;width:977px;height:1px;background:#555}
.copyright{position:absolute;left:0;top:2969px;width:1200px;text-align:center;font-size:11.5px}
</style>
</head>
<body>

<section class="hero">
  <div class="hero__photo" role="img" aria-label="Bouquet of pink tulips with a heart tag"></div>
  <svg class="abs" style="left:594px;top:86px" width="560" height="540" viewBox="0 0 560 540"><circle cx="270" cy="270" r="267" fill="none" stroke="#ef9d22" stroke-width="2"/></svg>
  <div class="hero__blob"></div>
  <div class="logo" style="left:100px;top:36px;font-size:26px"><span class="logo__dot"></span>Lantern Petals</div>
  <nav class="nav"><span>About Us</span><span>For Supermarkets</span><span>For Franchisees</span></nav>
  <a class="btn" style="left:961px;top:14px;width:126px;height:44px">Contact</a>
  <div class="abs hero__welcome">Welcome To</div>
  <div class="abs script hero__script">Lantern</div>
  <div class="abs hero__caps">PETALS</div>
  <a class="btn" style="left:110px;top:484px;width:127px;height:44px">Get Started</a>
</section>

<section class="about">
  <svg class="abs" style="left:98px;top:718px" width="452" height="452" viewBox="0 0 452 452"><circle cx="226" cy="226" r="223" fill="none" stroke="#ef9d22" stroke-width="3"/></svg>
  <div class="about__photo" role="img" aria-label="Hand holding a bouquet of pink and white carnations"></div>
  <h2 class="section-title script" style="left:638px;top:712px"><span class="orange">About</span> <span class="green">Us</span></h2>
  <div class="abs body-text" style="left:644px;top:821px;width:450px">
    <p>Fresh flowers convey beauty and love, and in our view should become something every person regularly enjoys.&nbsp; Lantern Petals is an entrepreneurial company created to make top quality fresh flowers and professionally-designed bouquets accessible to every consumer at affordable prices.</p>
    <p>Professional florists typically sell the finest quality stems, design the most beautiful bouquets and provide the finest customer service, but their costs – of floral products, retail spaces, labor and marketing – force them to pass high prices along to customers.</p>
  </div>
  <a class="btn" style="left:643px;top:1077px;width:126px;height:44px">Read More</a>
</section>

<section class="market" role="img" aria-label="Soft background of pale lilac flowers"></section>
<h2 class="section-title script" style="left:96px;top:1286px"><span class="orange">For</span> <span class="green">Supermarkets</span></h2>
<div class="abs body-text" style="left:110px;top:1398px;width:530px">
  <p>Lantern Petals works with some of the country's largest and most progressive supermarkets to provide franchisee ownership and operation of their strategically important floral departments.Supermarkets find that Lantern Petals is able to improve their financial outcomes, provide attentive customer service and satisfaction, and lift the quality of the entire store environment.</p>
</div>
<div class="link-heading">Opportunity for Supermarkets</div>
<ul class="checklist">
  <li><svg width="22" height="20" viewBox="0 0 22 20"><circle cx="9" cy="11" r="8" fill="none" stroke="#128a3c" stroke-width="2"/><path d="M4 11l5 5L21 2" fill="none" stroke="#128a3c" stroke-width="3"/></svg>Enhance floral revenue streams with efficient assortments and new offerings</li>
  <li><svg width="22" height="20" viewBox="0 0 22 20"><circle cx="9" cy="11" r="8" fill="none" stroke="#128a3c" stroke-width="2"/><path d="M4 11l5 5L21 2" fill="none" stroke="#128a3c" stroke-width="3"/></svg>Reduce the costs of operating a floral department</li>
  <li><svg width="22" height="20" viewBox="0 0 22 20"><circle cx="9" cy="11" r="8" fill="none" stroke="#128a3c" stroke-width="2"/><path d="M4 11l5 5L21 2" fill="none" stroke="#128a3c" stroke-width="3"/></svg>Improve the quality, useful life and merchandising of floral products</li>
  <li><svg width="22" height="20" viewBox="0 0 22 20"><circle cx="9" cy="11" r="8" fill="none" stroke="#128a3c" stroke-width="2"/><path d="M4 11l5 5L21 2" fill="none" stroke="#128a3c" stroke-width="3"/></svg>Maintain a beautiful, fresh and well-stocked environment</li>
</ul>
<a class="btn" style="left:108px;top:1742px;width:126px;height:44px">Read More</a>
<svg class="abs" style="left:660px;top:1370px" width="510" height="410" viewBox="660 1370 510 410">
  <defs>
    <linearGradient id="hexPurple" x1="0" y1="0" x2="1" y2="1"><stop offset="0" stop-color="#b9a2d8"/><stop offset="1" stop-color="#8a6cb8"/></linearGradient>
    <linearGradient id="hexYellow" x1="0" y1="0" x2="0" y2="1"><stop offset="0" stop-color="#f2dc4a"/><stop offset="1" stop-color="#cfe0f4"/></linearGradient>
    <linearGradient id="hexMixed" x1="0" y1="0" x2="1" y2="1"><stop offset="0" stop-color="#e2684a"/><stop offset="1" stop-color="#3b4458"/></linearGradient>
    <linearGradient id="hexPeach" x1="0" y1="0" x2="0" y2="1"><stop offset="0" stop-color="#f2a9a0"/><stop offset="1" stop-color="#5a6472"/></linearGradient>
  </defs>
  <g role="img" aria-label="Bouquet of purple roses"><polygon points="865,1385 960,1440 960,1549 865,1604 770,1549 770,1440" fill="url(#hexPurple)"/></g>
  <g role="img" aria-label="Hand holding yellow tulips"><polygon points="1063,1370 1158,1425 1158,1534 1063,1589 968,1534 968,1425" fill="url(#hexYellow)"/></g>
  <g role="img" aria-label="Colourful wrapped bouquet in a hand"><polygon points="758,1555 853,1610 853,1719 758,1774 663,1719 663,1610" fill="url(#hexMixed)"/></g>
  <g role="img" aria-label="Peach roses wrapped in paper cone"><polygon points="968,1555 1063,1610 1063,1719 968,1774 873,1719 873,1610" fill="url(#hexPeach)"/></g>
</svg>

<section class="franch">
  <svg class="abs" style="left:180px;top:2065px" width="260" height="260" viewBox="0 0 260 260"><circle cx="130" cy="130" r="127" fill="none" stroke="#ef9d22" stroke-width="3"/></svg>
  <div class="franch__photo" role="img" aria-label="Gerbera daisies in a glass vase beside red tulips"></div>
  <h2 class="section-title script" style="left:642px;top:1904px"><span class="orange">For</span> <span class="green">Franchisees</span></h2>
  <div class="abs body-text" style="left:644px;top:2010px;width:460px">
    <p>Lantern Petals brings the best of professional florists and supermarkets together for the benefit of consumers.&nbsp; It sutpports a national network of owner-operator franchisees, who in many cases are multi-site professional florists, with comprehensive services to enhance franchise profitability.</p>
    <p>Lantern Petals works with some of the country's largest and most progressive supermarkets to provide franchisee ownership and operation of their strategically important floral departments.</p>
  </div>
  <a class="btn" style="left:643px;top:2221px;width:126px;height:44px">Read More</a>
</section>

<div class="inquiry-band"></div>
<section class="inquiry">
  <div class="inquiry__photo" role="img" aria-label="Pink roses wrapped in kraft paper"></div>
  <h2 class="inquiry__title script">Do You Have<br>Any Doubts?</h2>
  <a class="btn btn--green" style="left:43px;top:201px;width:237px;height:44px">New Florist Franchise Inquiry</a>
  <a class="btn" style="left:287px;top:201px;width:295px;height:44px">Professional Florist Franchise Inquiry</a>
</section>

<footer class="footer">
  <div class="logo" style="left:108px;top:60px;font-size:30px"><span class="logo__dot"></span>Lantern Petals</div>
  <h4 style="left:479px;top:72px">Quick Links</h4>
  <ul class="quick" style="left:484px;top:105px"><li>About Us</li><li>For Supermarkets</li><li>For Franchisees</li><li>Contact</li></ul>
  <h4 style="left:699px;top:72px">Contact Info</h4>
  <ul class="contact" style="left:696px;top:96px">
    <li><span class="icon"><svg width="10" height="12" viewBox="0 0 10 12"><path d="M5 0a4 4 0 0 1 4 4c0 3-4 8-4 8S1 7 1 4a4 4 0 0 1 4-4z" fill="#fff"/><circle cx="5" cy="4" r="1.5" fill="#128a3c"/></svg></span>12 Garden Row, Ashby - 580214</li>
    <li><span class="icon"><svg width="11" height="11" viewBox="0 0 11 11"><path d="M2 0l2 2.5-1 1.5a7 7 0 0 0 4 4l1.5-1L11 9l-2 2C4 11 0 7 0 2z" fill="#fff"/></svg></span>+1 555 014 2738</li>
    <li><span class="icon"><svg width="11" height="8" viewBox="0 0 11 8"><rect width="11" height="8" fill="#fff"/><path d="M0 0l5.5 4.5L11 0" fill="none" stroke="#128a3c"/></svg></span>hello@lantern-petals.com</li>
  </ul>
  <h4 style="left:982px;top:72px">Follow Us</h4>
  <ul class="social" style="left:980px;top:102px">
    <li><span class="icon"></span>Petalbook</li>
    <li><span class="icon"></span>Chirper</li>
    <li><span class="icon"></span>Snapgram</li>
    <li><span class="icon"></span>WorkLink</li>
  </ul>
</footer>
<div class="email-field">Enter Email Address</div>
<a class="btn" style="left:110px;top:2897px;width:90px;height:30px;font-size:12px;font-weight:400">Subscribe</a>
<div class="rule"></div>
<div class="copyright">Copyright © Lantern Petals. All rights reserved.</div>

</body>
</html>
```